Veranix - Solution provider in business consulting

Veranix is a swiss based company providing solutions for developing markets. The business covers various fields of business consulting, such as supply chain, product costs, quality management and manufacturing management. The Business operates in a efficient, straight and solution oriented manner.
The final design should communicate these characteristics. Asian people as well as as western people shall identify the qualities of the company at first sight.
The customer needs business cards with a simple view but an recognizable design, printed in high quality. Engraved elements such as the globe or simple words are possible.
Available colors are: (RAL)
102/102/102
51/102/102
153/204/153
255/102/51
Font: Calibri

```html
<!DOCTYPE html>
<html lang="en">
<head>
<meta charset="utf-8">
<title>Veranix business cards</title>
<link href="https://fonts.googleapis.com/css2?family=Open+Sans:wght@300;400;600&display=swap" rel="stylesheet">
<style>
  :root {
    --stone: #666666;
    --paper: #ffffff;
    --backdrop: #e9e9e7;
    --ink-light: #ffffff;
  }
  * { margin: 0; padding: 0; box-sizing: border-box; }
  html, body {
    width: 1200px; height: 900px; overflow: hidden;
    background: var(--backdrop);
    font-family: "Open Sans", Calibri, Arial, sans-serif;
  }
  .canvas { position: relative; width: 1200px; height: 900px; }
  .card {
    position: absolute;
    box-shadow: 0 6px 18px rgba(0,0,0,0.18);
    overflow: hidden;
  }
  .card-front {
    left: 238px; top: 62px; width: 555px; height: 343px;
    background: var(--stone);
  }
  .card-back {
    left: 457px; top: 518px; width: 560px; height: 344px;
    background: var(--paper);
  }
  .map-area {
    position: absolute; left: 0; top: 0; width: 300px; height: 343px;
    background: var(--paper);
  }
  .wordmark {
    display: flex; align-items: center;
    color: var(--stone); font-weight: 300; letter-spacing: 0.5px;
  }
  .wordmark-dot {
    border-radius: 50%; background: var(--stone); flex: none;
  }
  .card-front .wordmark {
    position: absolute; left: 28px; top: 46px; font-size: 38px; gap: 10px;
  }
  .card-front .wordmark-dot { width: 26px; height: 26px; }
  .card-back .wordmark {
    position: absolute; left: 0; right: 0; top: 130px;
    justify-content: center; font-size: 62px; gap: 16px;
  }
  .card-back .wordmark-dot { width: 42px; height: 42px; }
  .contact {
    position: absolute; right: 30px; top: 72px;
    color: var(--ink-light); text-align: right;
  }
  .contact-name { font-size: 18px; font-weight: 600; line-height: 24px; }
  .contact-role { font-size: 14px; font-weight: 400; line-height: 20px; }
  .contact-lines { margin-top: 28px; list-style: none; }
  .contact-lines li {
    display: flex; justify-content: flex-end; align-items: center;
    gap: 8px; font-size: 14px; line-height: 24px;
  }
  .contact-lines svg { width: 11px; height: 11px; flex: none; }
  .contact-address { margin-top: 14px; font-size: 14px; line-height: 21px; }
</style>
</head>
<body>
<div class="canvas">
  <section class="card card-front">
    <div class="map-area" role="img" aria-label="White map silhouette of East and South-East Asia"></div>
    <div class="wordmark"><span>veranix</span><span class="wordmark-dot"></span></div>
    <div class="contact">
      <p class="contact-name">Marco Lindt</p>
      <p class="contact-role">CEO</p>
      <ul class="contact-lines">
        <li>+41 79 300 5812
          <svg viewBox="0 0 11 11"><rect x="2.5" y="0.5" width="6" height="10" rx="1" fill="none" stroke="#fff" stroke-width="1.2"/><rect x="4.5" y="8.3" width="2" height="1" fill="#fff"/></svg></li>
        <li>+41 71 640 3978
          <svg viewBox="0 0 11 11"><path d="M2 1 L4 1 L5 3.5 L3.7 4.6 Q5 7 6.4 7.3 L7.5 6 L10 7 L10 9 Q9.5 10 8.5 10 Q1 9 1 2 Q1 1 2 1Z" fill="#fff"/></svg></li>
        <li>marco.lindt@veranix.ch
          <svg viewBox="0 0 11 11"><rect x="0.5" y="2" width="10" height="7" fill="#fff"/><path d="M0.5 2 L5.5 6 L10.5 2" fill="none" stroke="#666" stroke-width="1"/></svg></li>
        <li>www.veranix.ch
          <svg viewBox="0 0 11 11"><circle cx="5.5" cy="5.5" r="5" fill="#fff"/><ellipse cx="5.5" cy="5.5" rx="2" ry="5" fill="none" stroke="#666" stroke-width="0.8"/><line x1="0.5" y1="5.5" x2="10.5" y2="5.5" stroke="#666" stroke-width="0.8"/></svg></li>
      </ul>
      <p class="contact-address">Veranix GmbH Feldweg 14<br>9247 Talwil Switzerland</p>
    </div>
  </section>

  <section class="card card-back">
    <div class="wordmark"><span>veranix</span><span class="wordmark-dot"></span></div>
  </section>
</div>
</body>
</html>
```